Business Card for Coastal Tundrabridge Advisory

We need a business card for Coastal Tundrabridge Advisory. The company website address is provided below. The company logo is attached. We provide specialized permafrost services to the mining, transportation, and oil & gas industries. The card should be prepared for:
Matthias Korhonen, PhD.
Coastal Tundrabridge Advisory
PO Box 418259
Quillwater, Alaska 99642
Direct: +1-907-555-0143
Email: mkorhonen@tundrabridgeadvisory.example
Website: www.coastaltundrabridgeadvisory.example

```html
<!DOCTYPE html>
<html lang="en">
<head>
<meta charset="utf-8">
<title>Coastal Tundrabridge Advisory – Business Card</title>
<link href="https://fonts.googleapis.com/css2?family=Open+Sans:wght@300;400;600&family=Roboto:wght@500&display=swap" rel="stylesheet">
<style>
  :root {
    --backdrop: #262626;
    --card: #0f1520;
    --card-edge: #141c29;
    --ink: #f2f4f7;
    --ink-soft: #cfd6df;
    --accent: #2f7fb3;
    --accent-deep: #1b3a55;
  }
  * { box-sizing: border-box; margin: 0; padding: 0; }
  html, body {
    width: 1200px; height: 780px; overflow: hidden;
    background: var(--backdrop);
    font-family: "Open Sans", Arial, sans-serif;
    color: var(--ink);
  }
  .canvas {
    position: relative; width: 1200px; height: 780px;
  }
  .card {
    position: absolute; top: 235px;
    width: 540px; height: 309px;
    background: var(--card);
    box-shadow: 0 18px 40px rgba(0,0,0,.55);
    overflow: hidden;
  }
  .card--front { left: 40px; }
  .card--back { left: 620px; }

  /* Front */
  .front-name {
    position: absolute; left: 24px; bottom: 24px;
    transform-origin: left bottom;
    transform: rotate(-90deg) translate(0, 100%);
    white-space: nowrap;
  }
  .front-name .given { font-weight: 600; font-size: 30px; }
  .front-name .family { font-weight: 300; font-size: 30px; }
  .front-name .degree { display: block; font-size: 14px; font-weight: 400; margin-top: 2px; }
  .front-brand {
    position: absolute; left: 130px; top: 34px;
    font-size: 24px; font-weight: 600; letter-spacing: .5px;
    display: flex; align-items: center; gap: 10px;
  }
  .front-brand .mark { width: 12px; height: 12px; background: var(--ink); }
  .front-address {
    position: absolute; right: 34px; top: 110px;
    text-align: right; font-size: 13px; line-height: 1.45; color: var(--ink-soft);
  }
  .front-contact {
    position: absolute; right: 34px; top: 170px;
    list-style: none; font-size: 13px; line-height: 1.75; color: var(--ink-soft);
  }
  .front-contact li { display: flex; justify-content: flex-end; align-items: center; gap: 8px; }
  .front-contact svg { width: 12px; height: 12px; fill: var(--ink); flex: none; }

  /* Back */
  .back-pattern {
    position: absolute; inset: 0;
    background:
      linear-gradient(200deg, rgba(47,127,179,0) 30%, rgba(47,127,179,.35) 55%, rgba(47,127,179,0) 80%),
      linear-gradient(180deg, #121a27 0%, #0f1520 100%);
  }
  .back-brand {
    position: absolute; left: 50%; top: 78px; transform: translateX(-50%);
    font-size: 16px; font-weight: 600; white-space: nowrap;
  }
  .back-services {
    position: absolute; left: 0; right: 0; bottom: 30px; text-align: center;
  }
  .back-services h2 {
    font-family: "Roboto", Arial, sans-serif; font-weight: 500;
    font-size: 14px; letter-spacing: .3px; margin-bottom: 6px;
  }
  .back-services p { font-size: 12px; color: var(--ink-soft); }
</style>
</head>
<body>
<main class="canvas">
  <section class="card card--front" aria-label="Business card front">
    <div class="front-name">
      <span class="degree">PhD</span>
      <span class="given">Matthias</span> <span class="family">Korhonen</span>
    </div>
    <div class="front-brand"><span class="mark"></span>Coastal Tundrabridge Advisory</div>
    <address class="front-address">PO Box 418259<br>Quillwater, Alaska 99642</address>
    <ul class="front-contact">
      <li>+1-907-555-0143
        <svg viewBox="0 0 24 24" aria-hidden="true"><path d="M6.6 10.8a15 15 0 006.6 6.6l2.2-2.2c.3-.3.7-.4 1-.2 1.1.4 2.3.6 3.6.6.6 0 1 .4 1 1V20c0 .6-.4 1-1 1A17 17 0 013 4c0-.6.4-1 1-1h3.5c.6 0 1 .4 1 1 0 1.3.2 2.5.6 3.6.1.3 0 .7-.2 1z"/></svg></li>
      <li>mkorhonen@tundrabridgeadvisory.example
        <svg viewBox="0 0 24 24" aria-hidden="true"><path d="M2 5h20v14H2z M4 7v.5l8 5 8-5V7l-8 5z" fill-rule="evenodd"/></svg></li>
      <li>www.coastaltundrabridgeadvisory.example
        <svg viewBox="0 0 24 24" aria-hidden="true"><circle cx="12" cy="12" r="10"/></svg></li>
    </ul>
  </section>

  <section class="card card--back" aria-label="Business card back">
    <div class="back-pattern" role="img" aria-label="Repeating company name pattern in blue tones"></div>
    <div class="back-brand">Coastal Tundrabridge Advisory</div>
    <div class="back-services">
      <h2>OUR SERVICES</h2>
      <p>We provide specialized permafrost services to the mining, transportation, and oil &amp; gas industries</p>
    </div>
  </section>
</main>
</body>
</html>
```